Business card design for Automotive workshop

We need a business card for a new automotive repair and tyre shop called Keelstone Prime Automotive located in New Zealand. We are a clean, modern and fresh workshop and company.

Front needs to feature logo,
my name:
Marlo Fenwicke (director)

Address:
48 Tarn Lane
Whitianga 3510

Phone: 07 594 2713
Mobile: 027 451 9362
Email: office@keelstoneautomotive.example.nz
Website: keelstoneautomotive.example.nz

Back needs to feature an area to write down appointment details, date and time.

Also feature a list of jobs and work we do such as,
Vehicle Servicing
All Mechanical Repairs
Warrant of Fitness
Tyres & Wheel Alignments
Automotive Diagnostics
Automotive Parts & Supplies

```html
<!DOCTYPE html>
<html lang="en">
<head>
<meta charset="utf-8">
<title>Keelstone Prime Automotive – Business Card</title>
<link href="https://fonts.googleapis.com/css2?family=Roboto:ital,wght@0,300;0,400;0,700;1,400&display=swap" rel="stylesheet">
<style>
  :root {
    --stage: #3a3431;
    --card: #2a2a2c;
    --card-edge: #e0232a;
    --red: #e3262d;
    --white: #f2f2f2;
    --emboss: #4a4a4d;
    --line: #bdbdbd;
  }
  * { box-sizing: border-box; margin: 0; padding: 0; }
  html, body { width: 1200px; height: 847px; overflow: hidden; }
  body {
    background: var(--stage);
    font-family: "Roboto", Arial, sans-serif;
    position: relative;
  }
  .card {
    position: absolute;
    width: 520px;
    height: 300px;
    background: var(--card);
    border: 3px solid var(--card-edge);
    box-shadow: 0 10px 24px rgba(0,0,0,.45);
    overflow: hidden;
  }
  /* ---------- back ---------- */
  .card--back { left: 50px; top: 90px; }
  .brand {
    font-weight: 700;
    text-transform: uppercase;
    letter-spacing: 1px;
    line-height: 1.05;
  }
  .card--back .brand {
    position: absolute; left: 150px; top: 22px; width: 330px;
    text-align: right;
    color: var(--emboss);
    font-size: 30px;
  }
  .services {
    position: absolute; left: 14px; right: 14px; top: 104px;
    color: var(--white);
    font-size: 11px;
    text-align: center;
    line-height: 1.7;
    white-space: nowrap;
  }
  .services .dot { color: var(--red); margin: 0 4px; }
  .appointment-title {
    position: absolute; left: 0; right: 0; top: 160px;
    text-align: center;
    color: var(--red);
    font-size: 17px;
    font-weight: 400;
    letter-spacing: .5px;
  }
  .appointment-fields {
    position: absolute; left: 30px; right: 30px; top: 200px;
    display: flex; gap: 16px;
    color: var(--white);
    font-size: 13px;
  }
  .field { display: flex; align-items: flex-end; flex: 1; }
  .field-rule { flex: 1; border-bottom: 1px solid var(--line); margin-left: 6px; height: 12px; }
  .weekdays {
    position: absolute; left: 30px; right: 30px; top: 246px;
    display: flex; justify-content: space-between;
    color: var(--white); font-size: 13px;
    list-style: none;
  }
  .weekdays li { display: flex; align-items: center; gap: 6px; }
  .tickbox {
    width: 12px; height: 12px; border-radius: 50%;
    border: 1.5px solid var(--red);
  }
  /* ---------- front ---------- */
  .card--front { left: 630px; top: 450px; }
  .card--front .brand {
    position: absolute; right: 30px; top: 40px; width: 330px;
    text-align: right;
    color: var(--red);
    font-size: 28px;
  }
  .holder {
    position: absolute; left: 16px; top: 150px; width: 190px;
    text-align: right;
  }
  .holder-name { color: var(--red); font-weight: 700; font-size: 17px; text-transform: uppercase; white-space: nowrap; }
  .holder-role { color: var(--white); font-size: 14px; margin-top: 2px; }
  .holder-address { color: var(--white); font-size: 12.5px; margin-top: 12px; line-height: 1.4; white-space: nowrap; }
  .divider {
    position: absolute; left: 216px; top: 150px;
    width: 1.5px; height: 110px; background: var(--red);
  }
  .contacts {
    position: absolute; left: 230px; top: 156px;
    list-style: none;
    color: var(--white); font-size: 12px; line-height: 2;
  }
  .contacts li { display: flex; align-items: center; gap: 7px; white-space: nowrap; }
  .contacts svg { width: 12px; height: 12px; fill: var(--red); flex: none; }
</style>
</head>
<body>

<section class="card card--back" aria-label="Business card back">
  <div class="brand">Keelstone Prime Automotive</div>
  <p class="services">
    Vehicle Servicing<span class="dot">•</span>All Mechanical Repairs<span class="dot">•</span>Warrant of Fitness<br>
    Tyres &amp; Wheel Alignments<span class="dot">•</span>Automotive Diagnostics<span class="dot">•</span>Automotive Parts &amp; Supplies
  </p>
  <h2 class="appointment-title">APPOINTMENT</h2>
  <div class="appointment-fields">
    <div class="field">Date:<span class="field-rule"></span></div>
    <div class="field">Time:<span class="field-rule"></span></div>
  </div>
  <ul class="weekdays">
    <li><span class="tickbox"></span>Mon</li>
    <li><span class="tickbox"></span>Tue</li>
    <li><span class="tickbox"></span>Wed</li>
    <li><span class="tickbox"></span>Thu</li>
    <li><span class="tickbox"></span>Fri</li>
  </ul>
</section>

<section class="card card--front" aria-label="Business card front">
  <div class="brand">Keelstone Prime Automotive</div>
  <div class="holder">
    <div class="holder-name">Marlo Fenwicke</div>
    <div class="holder-role">director</div>
    <div class="holder-address">48 Tarn Lane, Whitianga 3510</div>
  </div>
  <div class="divider"></div>
  <ul class="contacts">
    <li>
      <svg viewBox="0 0 24 24" aria-hidden="true"><path d="M6.6 10.8a15.1 15.1 0 0 0 6.6 6.6l2.2-2.2c.3-.3.7-.4 1-.2 1.1.4 2.3.6 3.6.6.6 0 1 .4 1 1V20c0 .6-.4 1-1 1C10.6 21 3 13.4 3 4c0-.6.4-1 1-1h3.5c.6 0 1 .4 1 1 0 1.3.2 2.5.6 3.6.1.3 0 .7-.2 1z"/></svg>
      07 594 2713
    </li>
    <li>
      <svg viewBox="0 0 24 24" aria-hidden="true"><path d="M7 1h10a2 2 0 0 1 2 2v18a2 2 0 0 1-2 2H7a2 2 0 0 1-2-2V3a2 2 0 0 1 2-2zm0 3v14h10V4zm5 15.5a1.2 1.2 0 1 0 0 2.4 1.2 1.2 0 0 0 0-2.4z"/></svg>
      027 451 9362
    </li>
    <li>
      <svg viewBox="0 0 24 24" aria-hidden="true"><path d="M2 5h20v14H2zm2 2v.5l8 5 8-5V7l-8 5z"/></svg>
      office@keelstoneautomotive.example.nz
    </li>
    <li>
      <svg viewBox="0 0 24 24" aria-hidden="true"><path d="M12 2a10 10 0 1 0 0 20 10 10 0 0 0 0-20zm6.9 9h-3a15 15 0 0 0-1.3-5.6A8 8 0 0 1 18.9 11zM12 4c.9 1.3 1.8 3.8 1.9 7h-3.8C10.2 7.8 11.1 5.3 12 4zM9.4 5.4A15 15 0 0 0 8.1 11h-3a8 8 0 0 1 4.3-5.6zM5.1 13h3a15 15 0 0 0 1.3 5.6A8 8 0 0 1 5.1 13zM12 20c-.9-1.3-1.8-3.8-1.9-7h3.8c-.1 3.2-1 5.7-1.9 7zm2.6-1.4a15 15 0 0 0 1.3-5.6h3a8 8 0 0 1-4.3 5.6z"/></svg>
      keelstoneautomotive.example.nz
    </li>
  </ul>
</section>

</body>
</html>
```